Modern looking signage for dental office.

Exterior signage for passing cars
Updates
Need extra days to review
Target Market(s)
Cars passing by
Font styles to use
Sans Serif
Colors
3276b5
Requirements
Must have
- Logo
- OPEN ON SUTURDAY AND SUNDAY
- NIGHT CLINIC AVAILABLE
- PLEASE USE THE FONT TYPE IN FILE 4 UPLOADED BELOW.
- (847) 302-7469
- Modern looking

```html
<!DOCTYPE html>
<html lang="en">
<head>
<meta charset="utf-8">
<title>Nova Dental – Weekend &amp; Night Clinic Sign</title>
<link href="https://fonts.googleapis.com/css2?family=Josefin+Sans:wght@300&family=Encode+Sans+Semi+Condensed:wght@400&family=Montserrat:wght@400;500;800;900&family=Oswald:wght@500&display=swap" rel="stylesheet">
<style>
  :root {
    --backdrop: #a9a9a9;
    --sign-top: #ffffff;
    --sign-bottom: #e4e4e4;
    --ink: #0d0d0d;
    --brand-grey: #4b4b4b;
    --tagline-grey: #555555;
    --band-text: #ffffff;
    --ring: #6b6b6b;
  }
  * { margin: 0; padding: 0; box-sizing: border-box; }
  html, body {
    width: 1200px;
    height: 1000px;
    overflow: hidden;
    background: var(--backdrop);
  }
  .sign {
    position: absolute;
    left: 197px;
    top: 97px;
    width: 780px;
    height: 808px;
    overflow: hidden;
    background: linear-gradient(180deg, var(--sign-top) 0%, var(--sign-bottom) 100%);
  }
  .brand-mark {
    position: absolute;
    left: 65px;
    top: 67px;
    width: 146px;
    height: 146px;
    border: 2px solid var(--ring);
    border-radius: 50%;
  }
  .brand-name {
    position: absolute;
    left: 230px;
    top: 102px;
    font-family: "Josefin Sans", sans-serif;
    font-weight: 300;
    font-size: 86px;
    line-height: 1;
    letter-spacing: 1px;
    color: var(--brand-grey);
    white-space: nowrap;
    transform: scaleX(0.8);
    transform-origin: left top;
  }
  .brand-tagline {
    position: absolute;
    left: 276px;
    top: 186px;
    font-family: "Encode Sans Semi Condensed", sans-serif;
    font-weight: 400;
    font-size: 30px;
    line-height: 1;
    color: var(--tagline-grey);
    white-space: nowrap;
  }
  .hours-panel {
    position: absolute;
    left: 74px;
    top: 276px;
    width: 660px;
    height: 385px;
    border: 2px solid var(--ink);
    background: transparent;
  }
  .open-days {
    height: 229px;
    text-align: center;
    color: var(--ink);
  }
  .open-days__lead {
    padding-top: 26px;
    font-family: "Montserrat", sans-serif;
    font-weight: 900;
    font-size: 112px;
    line-height: 1;
    letter-spacing: 1px;
  }
  .open-days__days {
    margin-top: 6px;
    font-family: "Oswald", sans-serif;
    font-weight: 500;
    font-size: 60px;
    line-height: 1;
    transform: scaleY(1.22);
  }
  .night-band {
    height: 152px;
    background: var(--ink);
    color: var(--band-text);
    text-align: center;
    font-family: "Montserrat", sans-serif;
  }
  .night-band__intro {
    padding-top: 26px;
    font-weight: 500;
    font-size: 46px;
    line-height: 1;
  }
  .night-band__hours {
    margin-top: 8px;
    font-weight: 800;
    font-size: 45px;
    line-height: 1;
  }
  .contact {
    position: absolute;
    left: 104px;
    top: 704px;
    display: flex;
    align-items: center;
    gap: 22px;
  }
  .contact__icon { width: 64px; height: 64px; }
  .contact__number {
    font-family: "Montserrat", sans-serif;
    font-weight: 800;
    font-size: 76px;
    line-height: 1;
    color: var(--ink);
    white-space: nowrap;
  }
</style>
</head>
<body>
  <main class="sign">
    <div class="brand-mark" aria-hidden="true"></div>
    <div class="brand-name">NOVA DENTAL</div>
    <div class="brand-tagline">MODERN GENERAL DENTISTRY</div>

    <section class="hours-panel">
      <div class="open-days">
        <div class="open-days__lead">OPEN ON</div>
        <div class="open-days__days">SATURDAY AND SUNDAY</div>
      </div>
      <div class="night-band">
        <div class="night-band__intro">NIGHT CLINIC FROM</div>
        <div class="night-band__hours">5PM TO 10PM AVAILABLE</div>
      </div>
    </section>

    <div class="contact">
      <svg class="contact__icon" viewBox="0 0 64 64" aria-hidden="true">
        <circle cx="32" cy="32" r="30" fill="none" stroke="#6b6b6b" stroke-width="2"/>
        <path d="M22 18c2-2 4-2 5 0l3 6c1 2 0 3-1 4l-2 2c2 4 5 7 9 9l2-2c1-1 2-2 4-1l6 3c2 1 2 3 0 5l-3 3c-3 2-9 1-16-6s-9-14-7-17z" fill="#0d0d0d"/>
        <path d="M36 20a10 10 0 0 1 9 9M36 14a16 16 0 0 1 15 15" fill="none" stroke="#0d0d0d" stroke-width="2.5" stroke-linecap="round"/>
      </svg>
      <div class="contact__number">847 302 7469</div>
    </div>
  </main>
</body>
</html>
```